Business Card Design for Occupational Medicine Start Up Company

We need to design a professional business card. We are a healthcare company providing occupational medicine services to blue collar industries. We are professional, efficient and high quality service providers.

Target Market(s)

Blue Collar Industry: Shipbuilding, Ports, Trucking Companies; The Executives and Safety Officers for these companies

Industry/Entity Type

Healthcare

Contact Information for Business Card

Logo, Name, Title, Email, Phone

Other font styles liked:
• Please match our Brand Guide

Requirements
Must have
• Our Company Colors and Logo

```html
<!DOCTYPE html>
<html lang="en">
<head>
<meta charset="utf-8">
<title>Harborline Health – Business Card</title>
<link rel="stylesheet" href="https://fonts.googleapis.com/css2?family=Montserrat:wght@500;700&family=Questrial&display=swap">
<style>
  :root {
    --page-bg: #3a3b3d;
    --card-bg: #1c1d1f;
    --pattern-bg: #151617;
    --ink-white: #ffffff;
    --ink-soft: #c9cacc;
    --ink-muted: #8e9093;
    --divider: #55575a;
    --band-light: #b9babc;
    --band-dark: #8a8b8e;
  }
  * { box-sizing: border-box; margin: 0; padding: 0; }
  html, body {
    width: 1200px; height: 1024px; overflow: hidden;
    background: var(--page-bg);
  }
  .stage {
    width: 1200px; height: 1024px;
    display: flex; flex-direction: column; align-items: center; justify-content: center;
    gap: 52px;
  }
  .card {
    position: relative;
    width: 760px; height: 434px;
    background: var(--card-bg);
    box-shadow: 0 14px 30px rgba(0,0,0,.45);
    overflow: hidden;
  }

  /* Back side */
  .card-back { background: var(--pattern-bg); }
  .back-pattern {
    position: absolute; inset: 0;
    background: linear-gradient(135deg, #1a1b1d 0%, #131415 100%);
  }
  .back-mark {
    position: absolute; right: 150px; top: 196px;
    display: flex; align-items: center; gap: 10px;
    font-family: "Montserrat", sans-serif; font-weight: 700;
    font-size: 16px; letter-spacing: 1px; color: var(--ink-white);
  }

  /* Front side */
  .brand {
    position: absolute; left: 0; top: 0; width: 360px; height: 420px;
    display: flex; flex-direction: column; align-items: center; justify-content: center; gap: 14px;
  }
  .brand-dot {
    width: 54px; height: 54px; border-radius: 50%;
    background: var(--band-light);
  }
  .back-mark .brand-dot { width: 22px; height: 22px; }
  .brand-name {
    font-family: "Montserrat", sans-serif; font-weight: 700;
    color: var(--ink-white); font-size: 26px; letter-spacing: 1px;
    text-align: center; line-height: 1.15;
  }
  .divider {
    position: absolute; left: 372px; top: 110px;
    width: 1px; height: 190px; background: var(--divider);
  }
  .contact-block {
    position: absolute; left: 410px; top: 118px;
  }
  .person-name {
    font-family: "Montserrat", sans-serif; font-weight: 700;
    font-size: 26px; color: var(--ink-white); letter-spacing: .5px;
  }
  .person-title {
    font-family: "Questrial", sans-serif;
    font-size: 14px; color: var(--ink-muted); margin-top: 2px;
  }
  .contact-list { list-style: none; margin-top: 22px; }
  .contact-item {
    display: flex; align-items: center; gap: 10px;
    font-family: "Questrial", sans-serif; font-size: 17px;
    color: var(--ink-soft); margin-bottom: 7px;
  }
  .contact-icon {
    width: 16px; height: 16px; border-radius: 50%;
    background: var(--ink-muted);
    display: flex; align-items: center; justify-content: center; flex: none;
  }
  .contact-icon svg { width: 10px; height: 10px; fill: var(--card-bg); }
  .footer-band {
    position: absolute; left: 0; bottom: 0; width: 100%; height: 14px;
    display: flex;
  }
  .band-dark { flex: 0 0 520px; background: var(--band-dark); }
  .band-gap { flex: 0 0 8px; background: var(--card-bg); }
  .band-light { flex: 1; background: var(--band-light); }
</style>
</head>
<body>
<main class="stage">
  <section class="card card-back" aria-label="Card back">
    <div class="back-pattern" role="img" aria-label="Repeating embossed brand pattern in dark tones"></div>
    <div class="back-mark"><span class="brand-dot"></span>HARBORLINE</div>
  </section>

  <section class="card card-front" aria-label="Card front">
    <div class="brand">
      <span class="brand-dot"></span>
      <div class="brand-name">HARBORLINE<br>HEALTH</div>
    </div>
    <div class="divider"></div>
    <div class="contact-block">
      <h1 class="person-name">DANIEL REYES</h1>
      <p class="person-title">Executive Manage</p>
      <ul class="contact-list">
        <li class="contact-item">
          <span class="contact-icon"><svg viewBox="0 0 10 10"><path d="M2 1l2 2-1 1.2c.6 1.2 1.6 2.2 2.8 2.8L7 6l2 2-1.2 1.5C4.5 9.2.8 5.5.5 2.2z"/></svg></span>
          555-010-0199
        </li>
        <li class="contact-item">
          <span class="contact-icon"><svg viewBox="0 0 10 10"><path d="M1 2.5h8v5H1z M1 2.5l4 3 4-3" stroke="#1c1d1f" stroke-width=".6"/></svg></span>
          info@harborlinehealth.com
        </li>
        <li class="contact-item">
          <span class="contact-icon"><svg viewBox="0 0 10 10"><path d="M5 1l4 3.5H8V9H6V6.5H4V9H2V4.5H1z"/></svg></span>
          Your address, your city, box 88900
        </li>
      </ul>
    </div>
    <div class="footer-band">
      <span class="band-dark"></span><span class="band-gap"></span><span class="band-light"></span>
    </div>
  </section>
</main>
</body>
</html>
```